Stationery Design Project for Nimbora, Chicago

Nimbora, a street parking application which helps car drivers find a street parking spot by offering an ideal path along which to look for parking. This path is calculated by our algorithm based on data (e.g. historical data, baseball games schedule, etc.). Along this path the driver will find a spot and will also save 70% of the search time. Customer we target is reg. between 21 and 45 yo.

We envision something young, fresh, bright and original. Slightly abstract maybe. It should represent the idea and elements of finding street parking in the city, e.g. car(s), parking spot, people, city, etc. (just ideas!).

Logo is attached.

Requirement:
- Business Cards (2 Sided Full Color CMYK)
- Letterhead (1 Sided Full Color CMYK)
- Envelope (1 Sided Full Color CMYK)
- Sticker (1 Sided Full Color CMYK), round with a 2inch diameter.

Reason: We're starting to get more and more designs and need more time to look into all of them. Very exciting!! Thanks to everybody!

Hi all, we're in the process of selecting our favs. Though choices!!! Really good submissions. Will keep you posted and sorry for the delay.

Target Market(s)

Car drivers and owners between 21 and 45

Industry/Entity Type

Parking

Requirements
Must have
• Sticker should be round and include company URL nimbora.com and the new logo which we will attach soon.
Should not have
• Should not be too serious or boring.

```html
<!DOCTYPE html>
<html lang="en">
<head>
<meta charset="utf-8">
<title>Nimbora Business Card</title>
<link rel="stylesheet" href="https://fonts.googleapis.com/css2?family=Source+Sans+3:wght@400;600;700&display=swap">
<style>
  :root {
    --page: #e4e6ea;
    --card: #ffffff;
    --ink: #1a1a1a;
    --ink-soft: #2b2b2b;
    --brand-blue: #2d4fae;
    --brand-blue-deep: #1f3a8f;
    --brand-blue-light: #3f7fd6;
    --band-black: #111111;
    --band-grey: #5a5a5a;
    --photo-light: #d9d9d9;
    --photo-mid: #9a9c9f;
    --photo-dark: #5d6064;
  }
  * { margin: 0; padding: 0; box-sizing: border-box; }
  html, body {
    width: 954px; height: 1200px; overflow: hidden;
    background: var(--page);
    font-family: "Source Sans 3", "Myriad Pro", sans-serif;
  }
  .canvas { position: relative; width: 954px; height: 1200px; }

  .card {
    position: absolute; left: 63px; width: 795px; height: 456px;
    background: var(--card); border-radius: 28px; overflow: hidden;
    box-shadow: 0 6px 18px rgba(0,0,0,.22);
  }
  .card--front { top: 100px; }
  .card--back { top: 649px; }

  .card__swoosh { position: absolute; inset: 0; width: 795px; height: 456px; }

  .brand-dot {
    position: absolute; width: 160px; height: 160px; border-radius: 50%;
    background: radial-gradient(circle at 40% 35%, var(--brand-blue-light), var(--brand-blue-deep) 75%);
    box-shadow: 0 0 0 8px #eef1f6;
  }
  .card--front .brand-dot { left: 114px; top: 36px; }
  .card--back .brand-dot { left: 63px; top: 102px; }

  .wordmark {
    position: absolute; left: 300px; top: 44px;
    font-size: 104px; font-weight: 700; line-height: 1; color: var(--ink-soft);
    letter-spacing: -1px;
  }

  .identity {
    position: absolute; left: 0; right: 0; top: 210px; text-align: center;
    font-size: 25px; font-weight: 700; color: var(--ink);
  }
  .contacts {
    position: absolute; left: 0; right: 0; top: 276px; text-align: center;
    font-size: 18.5px; line-height: 27px; color: var(--ink);
  }
  .contacts b { font-weight: 700; }
  .contacts .sep { padding: 0 6px; }

  .address {
    position: absolute; right: 56px; top: 405px;
    font-size: 19.5px; color: #ffffff;
  }

  .photo {
    position: absolute; left: 256px; top: 22px; width: 498px; height: 316px;
    background:
      radial-gradient(ellipse at 65% 45%, var(--photo-mid), transparent 70%),
      linear-gradient(135deg, var(--photo-dark), var(--photo-mid) 55%, var(--photo-light));
    -webkit-mask-image: radial-gradient(ellipse 62% 62% at 55% 48%, #000 60%, transparent 100%);
    mask-image: radial-gradient(ellipse 62% 62% at 55% 48%, #000 60%, transparent 100%);
  }

  .website {
    position: absolute; left: 370px; top: 392px;
    font-size: 26px; color: #ffffff; letter-spacing: 1px;
  }
  .website__name { letter-spacing: 7px; }
</style>
</head>
<body>
<div class="canvas">

  <section class="card card--front">
    <svg class="card__swoosh" viewBox="0 0 795 456" aria-hidden="true">
      <defs>
        <linearGradient id="frontBlue" x1="0" y1="0" x2="1" y2="0">
          <stop offset="0" stop-color="#3d7fd8"/>
          <stop offset="0.45" stop-color="#2d4fae"/>
          <stop offset="1" stop-color="#233f96"/>
        </linearGradient>
        <linearGradient id="frontBlack" x1="0" y1="0" x2="1" y2="0">
          <stop offset="0" stop-color="#6a6a6a"/>
          <stop offset="0.3" stop-color="#111"/>
          <stop offset="1" stop-color="#111"/>
        </linearGradient>
      </defs>
      <path d="M0 395 Q 190 360 410 344 Q 200 372 0 430 Z" fill="url(#frontBlack)"/>
      <path d="M0 456 L0 445 Q 260 360 500 342 Q 680 332 795 380 L795 456 Z" fill="url(#frontBlue)"/>
    </svg>
    <div class="brand-dot"></div>
    <div class="wordmark">Nimbora</div>
    <p class="identity">Your Name - Designation</p>
    <p class="contacts">
      <b>t</b> : 123-456-7890<span class="sep">|</span><b>m</b> : 123-456-7890<br>
      <b>e</b> : name@website.com<span class="sep">|</span><b>w</b> : www.website.com
    </p>
    <p class="address">City Name, Street Name, State Name, Country Code</p>
  </section>

  <section class="card card--back">
    <div class="photo" role="img" aria-label="Aerial photo of a city street with cars parked in marked parking spaces"></div>
    <svg class="card__swoosh" viewBox="0 0 795 456" aria-hidden="true">
      <defs>
        <linearGradient id="backBlack" x1="0" y1="0" x2="1" y2="0">
          <stop offset="0" stop-color="#111"/>
          <stop offset="0.7" stop-color="#1a1a1a"/>
          <stop offset="1" stop-color="#555"/>
        </linearGradient>
        <linearGradient id="backBlue" x1="0" y1="0" x2="1" y2="0">
          <stop offset="0" stop-color="#2d4fae"/>
          <stop offset="1" stop-color="#3f7fd6"/>
        </linearGradient>
      </defs>
      <path d="M0 390 Q 180 360 410 352 Q 200 372 0 430 Z" fill="url(#backBlue)"/>
      <path d="M0 456 L0 445 Q 260 360 500 352 Q 680 348 795 385 L795 456 Z" fill="url(#backBlack)"/>
    </svg>
    <div class="brand-dot"></div>
    <p class="website">www.<span class="website__name">WEBSITE</span>.com</p>
  </section>

</div>
</body>
</html>
```